Packaged Food Business Needs a Packaging Design

We need a package design to be used as a label/sticker on the lids of round and square transparent plastic containers and on the sides of resealable stand-up pouches. The brand name is 'Savorine' - please find attached logo together with pictures of the sample containers and pouch. We will use the packaging to market a wide variety of food categories from nuts, dried fruits, spices, cooking chocolates, baking ingredients, cereals, grains and pulses.

OVERALL FEEDBACK ON DESIGNS ALREADY RECEIVED:

- We have found so far that a lot of our mandatory requirements are not adhered to in designs that have been submitted so far. We would like to emphasise that the ingredient, weight and expiry text will be printed at the time of packing so it should not take prime space on the pack BUT at the same time some 'blank' space needs to flawlessly be incorporated into the overall design for this purpose
- We encourage you to glorify the brand logo in the pack, and absolutely refrain from duplicating the tagline
- Please note that ONE label design will be used to pack a wide variety of food ingredients and therefore please ensure that the choice of your design incorporates this requirement, in the past we have received designs that are limited to only one type of food (like nuts) or have received designs that are too floral or leafy (and not grounded to food
- Please ensure that you submit designs for all three packaging formats, it is critical to see the family look from the on-set

Target Market(s)

The brand is targeting both mothers and professional chefs and therefore the label design should be broadly approachable and convey affordable premium

Industry/Entity Type

Business

Requirements
Must have
• - Consistent with the brand name and logo, the overall look and feel of the packaging should convey values of healthy, gourmet food ingredients, high in nourishment and project a sense of delightful taste
• - The design styling to be modern and 'simplistic' (embracing 'less-is-more' type of a design style)
• - Design a packaging architecture that incorporates the brand logo together with its tagline lock-up of 'taste the goodness in every spoonful' - find logo attached
• - The design needs to have a dedicated area to print the ingredient (e.g., Mixed Nuts), weight (e.g., 500g) and expiry (this space needs to be flawlessly incorporated into the design) - this information will be printed either with an inkjet printer or with a rubber stamp so please leave an empty space (the text should not be part of the design, just the area for the text needs to be included in the design)
• - The packaging must include 'Packed By: Kestomar Traders Ltd, P. O. Box 51946, Kampala - Uganda'
• - For the design of the resealable pouch, please incorporate a window to see through the ingredients and a hole on top to hang on supermarket pegs if necessary
Nice to have
• - We would love to have some design submissions that are bold and cheerful and fun (but not frivolous) - please see attached inspiration for 'fun' packaging. The attachments are purely for inspiration, not to infringe on anyone else's TM and copyrights
• - Incorporate green to convey healthy, organic values
• - Explore use of gold and silver convey premiumness
Should not have
• - Do not duplicate the tagline
• - Do not include the ingredient, weight and expiry in the main graphic of the design, these will be printed at the time of packing so ensure there is provision for this in a flawless way in the design (e.g., via a blank space allocated for this purpose)

```html
<!DOCTYPE html>
<html lang="en">
<head>
<meta charset="utf-8">
<title>Savorine Packaging Labels</title>
<link rel="stylesheet" href="https://fonts.googleapis.com/css2?family=Oswald:wght@300;400;500;600&family=Montserrat:wght@700&display=swap">
<style>
  :root {
    --brown: #3b2312;
    --tag-green: #5a8a2a;
    --band-green: #9bbd4a;
    --tab-red: #e05a5a;
    --tab-text: #b83a3a;
    --window-grey: #5c5c5c;
    --white: #ffffff;
    --floral: linear-gradient(135deg, #f4c9c9 0%, #fbe9b8 28%, #cfe9ee 55%, #d6eac6 78%, #f1cde3 100%);
  }
  * { box-sizing: border-box; margin: 0; padding: 0; }
  html, body { width: 1200px; height: 1200px; overflow: hidden; background: var(--white); }
  .canvas { position: relative; width: 1200px; height: 1200px; }

  .floral-fill { position: absolute; inset: 0; background: var(--floral); }

  .print-tab {
    position: absolute; background: var(--tab-red); color: var(--tab-text);
    font-family: "Oswald", sans-serif; font-weight: 400; text-transform: uppercase;
  }
  .brand-panel {
    position: absolute; background: var(--white);
    display: flex; flex-direction: column; align-items: center; justify-content: flex-end;
  }
  .brand-name {
    font-family: "Oswald", sans-serif; font-weight: 600; color: var(--brown);
    text-transform: uppercase; line-height: 1;
  }
  .brand-tagline {
    font-family: "Montserrat", sans-serif; font-weight: 700; color: var(--tag-green);
    text-transform: uppercase; line-height: 1;
  }
  .packer-band {
    position: absolute; background: var(--band-green); color: var(--white);
    font-family: "Oswald", sans-serif; text-transform: uppercase;
    display: flex; align-items: center; white-space: nowrap;
  }
  .packer-band .lead { font-weight: 500; }
  .packer-band .address { font-weight: 300; }
  .packer-band .net { font-weight: 500; margin-left: auto; padding-left: 14px; }

  /* Round lid label */
  .lid-round {
    position: absolute; left: 80px; top: 200px; width: 395px; height: 395px;
    border-radius: 50%; overflow: hidden;
  }
  .lid-round .print-tab { left: 170px; top: 0; width: 61px; height: 85px; font-size: 8px; }
  .lid-round .print-tab span { position: absolute; left: 0; right: 0; text-align: center; }
  .lid-round .brand-panel { left: 0; top: 110px; width: 395px; height: 169px; padding-bottom: 16px; }
  .lid-round .brand-name { font-size: 58px; letter-spacing: 8px; margin-bottom: 6px; }
  .lid-round .brand-tagline { font-size: 10px; letter-spacing: 1.2px; }
  .lid-round .lid-band { position: absolute; left: 0; top: 350px; width: 395px; height: 45px; background: var(--band-green); }
  .lid-round svg { position: absolute; inset: 0; }
  .lid-round svg text { font-family: "Oswald", sans-serif; fill: var(--white); text-transform: uppercase; }

  /* Square lid label */
  .lid-square { position: absolute; left: 26px; top: 660px; width: 468px; height: 302px; overflow: hidden; }
  .lid-square .print-tab { left: 331px; top: 0; width: 104px; height: 46px; font-size: 8px; display: flex; }
  .lid-square .print-tab span { flex: 1; text-align: center; padding-top: 7px; }
  .lid-square .print-tab span + span { border-left: 1px solid var(--tab-text); }
  .lid-square .brand-panel { left: 6px; top: 65px; width: 456px; height: 172px; padding-bottom: 18px; }
  .lid-square .brand-name { font-size: 52px; letter-spacing: 8px; margin-bottom: 7px; }
  .lid-square .brand-tagline { font-size: 10px; letter-spacing: 1.3px; }
  .lid-square .packer-band { left: 0; top: 279px; width: 468px; height: 23px; padding: 0 52px 0 8px; }
  .lid-square .lead { font-size: 13px; margin-right: 6px; }
  .lid-square .address { font-size: 7px; }
  .lid-square .net { font-size: 13px; }

  /* Stand-up pouch */
  .pouch { position: absolute; left: 570px; top: 219px; width: 574px; height: 861px; overflow: hidden; }
  .pouch .hang-hole { position: absolute; left: 217px; top: 24px; width: 142px; height: 38px; background: var(--window-grey); border-radius: 14px; }
  .pouch .hang-hole::before {
    content: ""; position: absolute; left: 53px; top: -12px; width: 36px; height: 30px;
    background: var(--window-grey); border-radius: 18px 18px 0 0;
  }
  .pouch .print-tab { left: 434px; top: 0; width: 85px; height: 118px; font-size: 11px; }
  .pouch .print-tab span { position: absolute; left: 0; right: 0; text-align: center; }
  .pouch .brand-panel { left: 13px; top: 148px; width: 548px; height: 250px; padding-bottom: 24px; }
  .pouch .brand-name { font-size: 94px; letter-spacing: 14px; margin-bottom: 12px; }
  .pouch .brand-tagline { font-size: 16px; letter-spacing: 2.2px; }
  .pouch .see-window { position: absolute; left: 39px; top: 458px; width: 213px; height: 323px; background: var(--window-grey); border-radius: 12px; }
  .pouch .packer-band { left: 0; top: 809px; width: 574px; height: 52px; padding: 0 70px 0 15px; }
  .pouch .lead { font-size: 23px; margin-right: 6px; }
  .pouch .address { font-size: 10.5px; letter-spacing: -0.1px; }
  .pouch .net { font-size: 23px; }
</style>
</head>
<body>
<main class="canvas">

  <section class="lid-round" aria-label="Round lid label">
    <div class="floral-fill" role="img" aria-label="Colourful flat floral pattern with flowers, leaves and berries"></div>
    <div class="print-tab">
      <span style="top:12px">Ingredients</span>
      <span style="top:50px">Best Before</span>
    </div>
    <div class="brand-panel">
      <div class="brand-name">Savorine</div>
      <div class="brand-tagline">Taste the goodness in every spoonful!</div>
    </div>
    <div class="lid-band"></div>
    <svg viewBox="0 0 395 395" width="395" height="395">
      <defs>
        <path id="lid-arc" d="M 61.5 320 A 183 183 0 0 0 333.5 320"/>
      </defs>
      <text x="210" y="366" font-size="11" font-weight="500" text-anchor="middle">Net Weight</text>
      <text font-size="7.5" font-weight="400">
        <textPath href="#lid-arc" startOffset="50%" text-anchor="middle"><tspan font-size="9" font-weight="500">Packed By</tspan> Kestomar Traders Ltd, P. O. Box 51946, Kampala - Uganda</textPath>
      </text>
    </svg>
  </section>

  <section class="lid-square" aria-label="Square lid label">
    <div class="floral-fill" role="img" aria-label="Colourful flat floral pattern with flowers, leaves and berries"></div>
    <div class="print-tab">
      <span>Ingredients</span>
      <span>Best Before</span>
    </div>
    <div class="brand-panel">
      <div class="brand-name">Savorine</div>
      <div class="brand-tagline">Taste the goodness in every spoonful!</div>
    </div>
    <div class="packer-band">
      <span class="lead">Packed By</span>
      <span class="address">Kestomar Traders Ltd, P. O. Box 51946, Kampala - Uganda</span>
      <span class="net">Net Weight</span>
    </div>
  </section>

  <section class="pouch" aria-label="Stand-up pouch label">
    <div class="floral-fill" role="img" aria-label="Colourful flat floral pattern with flowers, leaves and berries"></div>
    <div class="hang-hole"></div>
    <div class="print-tab">
      <span style="top:17px">Ingredients</span>
      <span style="top:70px">Best Before</span>
    </div>
    <div class="brand-panel">
      <div class="brand-name">Savorine</div>
      <div class="brand-tagline">Taste the goodness in every spoonful!</div>
    </div>
    <div class="see-window"></div>
    <div class="packer-band">
      <span class="lead">Packed By</span>
      <span class="address">Kestomar Traders Ltd, P. O. Box 51946, Kampala - Uganda</span>
      <span class="net">Net Weight</span>
    </div>
  </section>

</main>
</body>
</html>
```